Need help in designing new business card utilizing our new logo.

BuildMark Solutions works with Construction Business Owners, Managers & IT Professionals to strengthen software usage and increase user productivity.

Our Construction Accounting and Mobile Field Management Software Clients engage with us in the following areas:

New Software Implementations
Software Re-Implementations
Redesigning Software Usage at the User Level
Project Coordination & Management
Continued Software Support

Old tag line:
Weighing Options - Implementing Solutions

www.buildmark-solutions.example

Ridge 4 is a product, but not needed for a new business card.

```html
<!DOCTYPE html>
<html lang="en">
<head>
<meta charset="utf-8">
<title>BuildMark Solutions — Business Card</title>
<link rel="stylesheet" href="https://fonts.googleapis.com/css2?family=Roboto:wght@400;500&family=Roboto+Condensed:wght@700&display=swap">
<style>
  :root {
    --brand-blue: #0b1ea0;
    --brand-blue-deep: #07168a;
    --band-grey: #b9b9bb;
    --card-white: #f3f3f4;
    --ink: #2b2b2e;
    --ink-soft: #4a4a4f;
    --page: #c4c4c6;
    --white: #ffffff;
  }
  * { box-sizing: border-box; margin: 0; padding: 0; }
  html, body {
    width: 1200px; height: 576px; overflow: hidden;
    background: var(--page);
    font-family: "Roboto", Arial, sans-serif;
  }
  .canvas { position: relative; width: 1200px; height: 576px; }

  .card {
    position: absolute; top: 138px; width: 484px; height: 293px;
    border-radius: 11px; overflow: hidden;
  }

  /* Front */
  .card-front { left: 82px; background: linear-gradient(180deg, var(--brand-blue-deep), var(--brand-blue)); color: var(--white); }
  .front-brand {
    position: absolute; top: 0; left: 0; right: 0; height: 167px;
    display: flex; align-items: center; justify-content: center; gap: 12px;
  }
  .brand-square { width: 22px; height: 22px; background: currentColor; }
  .brand-name { font-weight: 500; font-size: 30px; letter-spacing: 0.5px; }
  .services-band {
    position: absolute; top: 167px; left: 0; right: 0; height: 80px;
    background: linear-gradient(180deg, #c6c6c8, var(--band-grey));
    color: var(--ink); font-size: 13px; line-height: 18.5px; text-align: center;
    display: flex; flex-direction: column; justify-content: center;
  }
  .services-band .sep { margin: 0 8px; }
  .front-web {
    position: absolute; top: 258px; left: 0; right: 0;
    display: flex; align-items: center; justify-content: center; gap: 20px;
    font-size: 11.5px;
  }
  .front-web .rule { width: 34px; height: 1px; background: rgba(255,255,255,0.75); }

  /* Back */
  .card-back { left: 602px; background: var(--card-white); }
  .tagline-strip {
    position: absolute; top: 0; left: 0; bottom: 0; width: 46px;
    background: var(--brand-blue); color: var(--white);
  }
  .tagline-strip span {
    position: absolute; left: 50%; top: 50%;
    transform: translate(-50%, -50%) rotate(-90deg);
    white-space: nowrap; font-size: 11px; letter-spacing: 0.2px;
  }
  .back-content { position: absolute; left: 66px; top: 0; right: 0; bottom: 0; color: var(--ink); }
  .back-brand {
    position: absolute; top: 34px; left: 0;
    display: flex; align-items: center; gap: 10px; color: var(--brand-blue);
  }
  .back-brand .brand-name { font-size: 28px; }
  .person-name {
    position: absolute; top: 118px; left: 0;
    font-family: "Roboto Condensed", Arial, sans-serif; font-weight: 700;
    font-size: 21px; color: var(--brand-blue);
  }
  .person-role { position: absolute; top: 145px; left: 0; font-size: 11.5px; color: var(--ink-soft); }
  .contact-list { position: absolute; top: 184px; left: 0; list-style: none; font-size: 11.5px; }
  .contact-list li { display: flex; align-items: center; gap: 9px; height: 17px; }
  .contact-list svg { width: 11px; height: 11px; fill: var(--brand-blue-deep); flex: none; }
  .contact-list .web-name { color: var(--brand-blue); }
  .address { position: absolute; top: 257px; left: 0; font-size: 11.5px; }
</style>
</head>
<body>
<div class="canvas">

  <section class="card card-front" aria-label="Card front">
    <div class="front-brand">
      <span class="brand-square"></span>
      <span class="brand-name">BuildMark Solutions</span>
    </div>
    <div class="services-band">
      <p>New Software Implementations<span class="sep">|</span>Software Re-Implementations</p>
      <p>Redesigning Software Usage at the User Level</p>
      <p>Project Coordination &amp; Management<span class="sep">|</span>Continued Software Support</p>
    </div>
    <div class="front-web">
      <span class="rule"></span>
      <span>www.buildmark-solutions.example</span>
      <span class="rule"></span>
    </div>
  </section>

  <section class="card card-back" aria-label="Card back">
    <div class="tagline-strip"><span>Weighing Options - Implementing Solutions</span></div>
    <div class="back-content">
      <div class="back-brand">
        <span class="brand-square"></span>
        <span class="brand-name">BuildMark Solutions</span>
      </div>
      <h1 class="person-name">Dana R. Whitfield</h1>
      <p class="person-role">Owner</p>
      <ul class="contact-list">
        <li>
          <svg viewBox="0 0 12 12" aria-hidden="true"><path d="M3 0h6a1 1 0 0 1 1 1v10a1 1 0 0 1-1 1H3a1 1 0 0 1-1-1V1a1 1 0 0 1 1-1zm0.6 1.3v8h4.8v-8zM6 9.8a.7.7 0 1 0 0 1.4.7.7 0 0 0 0-1.4z"/></svg>
          555-014-2837
        </li>
        <li>
          <svg viewBox="0 0 12 12" aria-hidden="true"><path d="M0 3.5C1 1.5 3.5 1 6 1s5 .5 6 2.5L10 5 8.6 3.6H3.4L2 5zM2.5 6h7l1 5h-9zM6 7a1.5 1.5 0 1 0 0 3 1.5 1.5 0 0 0 0-3z"/></svg>
          555-019-4420 ext. 100
        </li>
        <li>
          <svg viewBox="0 0 12 12" aria-hidden="true"><path d="M0 2h12v8H0zm1 1v.4l5 3.3 5-3.3V3zm0 1.6V9h10V4.6L6 8z"/></svg>
          dana.whitfield@buildmark-solutions.example
        </li>
        <li>
          <svg viewBox="0 0 12 12" aria-hidden="true"><path d="M6 0a6 6 0 1 0 0 12A6 6 0 0 0 6 0zm-.6 1.3C4.6 2.3 4.2 3.6 4.1 5.4H1.3a4.8 4.8 0 0 1 4.1-4.1zm1.2 0a4.8 4.8 0 0 1 4.1 4.1H7.9c-.1-1.8-.5-3.1-1.3-4.1zM5.3 5.4c.1-1.6.4-2.8.7-3.4.3.6.6 1.8.7 3.4zM1.3 6.6h2.8c.1 1.8.5 3.1 1.3 4.1a4.8 4.8 0 0 1-4.1-4.1zm4 0h1.4c-.1 1.6-.4 2.8-.7 3.4-.3-.6-.6-1.8-.7-3.4zm2.6 0h2.8a4.8 4.8 0 0 1-4.1 4.1c.8-1 1.2-2.3 1.3-4.1z"/></svg>
          <span>www.<span class="web-name">buildmark-solutions</span>.example</span>
        </li>
      </ul>
      <p class="address">14B Market Street - PMB 118 Lakeview, NY 12001</p>
    </div>
  </section>

</div>
</body>
</html>
```